Business card design for Automotive workshop

We need a business card for a new automotive repair and tyre shop called Keelstone Prime Automotive located in New Zealand. We are a clean, modern and fresh workshop and company.

Front needs to feature logo,
my name:
Marlo Fenwicke (director)

Address:
48 Tarn Lane
Harrowby 3597

Phone: 07 594 2713
Mobile: 027 451 9362
Email: office@keelstoneautomotive.example.nz
Website: keelstoneautomotive.example.nz

Back needs to feature an area to write down appointment details, date and time.

Also feature a list of jobs and work we do such as,
Vehicle Servicing
All Mechanical Repairs
Warrant of Fitness
Tyres & Wheel Alignments
Automotive Diagnostics
Automotive Parts & Supplies

```html
<!DOCTYPE html>
<html lang="en">
<head>
<meta charset="utf-8">
<title>Keelstone Prime Automotive – Business Card</title>
<link href="https://fonts.googleapis.com/css2?family=Open+Sans:wght@400;600;700&display=swap" rel="stylesheet">
<style>
  :root {
    --page-bg: #e9e6e2;
    --card-bg: #161313;
    --card-shade: #221e1e;
    --brand-red: #e2262d;
    --text-light: #f4f2f0;
    --field-white: #ffffff;
  }
  * { box-sizing: border-box; margin: 0; padding: 0; }
  html, body {
    width: 1200px; height: 900px; overflow: hidden;
    background: var(--page-bg);
    font-family: "Open Sans", Arial, sans-serif;
  }
  .sheet {
    width: 1200px; height: 900px;
    display: flex; flex-direction: column; align-items: center; justify-content: center;
    gap: 40px;
  }
  .card {
    position: relative;
    width: 660px; height: 378px;
    background: var(--card-bg);
    border-radius: 4px;
    box-shadow: 0 8px 24px rgba(0,0,0,0.25);
    overflow: hidden;
    color: var(--text-light);
  }
  .card__artwork {
    position: absolute; left: 0; top: 0;
    width: 390px; height: 100%;
    background: radial-gradient(ellipse at 55% 45%, var(--card-shade) 0%, var(--card-bg) 70%);
  }
  .brand {
    position: absolute; right: 36px; top: 34px;
    text-align: right;
    font-weight: 700; font-size: 27px; line-height: 1.05;
    letter-spacing: 1px; text-transform: uppercase;
    color: var(--brand-red);
  }
  .person {
    position: absolute; right: 36px; top: 124px; text-align: right;
  }
  .person__name { color: var(--brand-red); font-weight: 700; font-size: 20px; letter-spacing: 0.5px; }
  .person__role { font-size: 16px; font-weight: 400; margin-top: 2px; }
  .contact-list {
    position: absolute; right: 36px; top: 196px;
    list-style: none; text-align: right;
  }
  .contact-list li {
    display: flex; justify-content: flex-end; align-items: center; gap: 10px;
    font-size: 16px; line-height: 27px;
  }
  .contact-list svg { width: 16px; height: 16px; flex: none; }
  .service-list {
    position: absolute; right: 36px; top: 136px;
    list-style: none; text-align: right;
  }
  .service-list li {
    font-size: 16px; line-height: 29px;
    display: flex; justify-content: flex-end; align-items: center; gap: 10px;
  }
  .service-list li::after {
    content: ""; width: 6px; height: 6px; background: var(--brand-red); flex: none;
  }
  .appointment { position: absolute; display: flex; align-items: center; gap: 12px; }
  .appointment__label { color: var(--brand-red); font-size: 22px; }
  .appointment__field {
    height: 40px; border-radius: 20px; background: var(--field-white);
  }
  .appointment--date { left: 30px; top: 150px; }
  .appointment--date .appointment__field { width: 240px; }
  .appointment--time { left: 30px; top: 296px; }
  .appointment--time .appointment__field { width: 280px; }
</style>
</head>
<body>
<main class="sheet">

  <section class="card card--front" aria-label="Business card front">
    <div class="card__artwork" role="img" aria-label="Faint dark emblem artwork with spanner motif"></div>
    <div class="brand">Keelstone Prime<br>Automotive</div>
    <div class="person">
      <p class="person__name">Marlo Fenwicke</p>
      <p class="person__role">Managing Director</p>
    </div>
    <ul class="contact-list">
      <li>+ 027 451 9362
        <svg viewBox="0 0 16 16" fill="none" stroke="var(--brand-red)" stroke-width="1.6"><rect x="4" y="1" width="8" height="14" rx="1.5"/><line x1="7" y1="12.5" x2="9" y2="12.5"/></svg>
      </li>
      <li>+ 07 594 2713
        <svg viewBox="0 0 16 16" fill="var(--brand-red)"><path d="M2 6 Q8 1 14 6 L12 8 L10 6.5 L6 6.5 L4 8 Z"/><rect x="3" y="9" width="10" height="5" rx="1"/></svg>
      </li>
      <li>office@keelstoneautomotive.example.nz
        <svg viewBox="0 0 16 16" fill="none" stroke="var(--brand-red)" stroke-width="1.6"><rect x="1.5" y="3.5" width="13" height="9"/><polyline points="1.5,3.5 8,9 14.5,3.5"/></svg>
      </li>
      <li>keelstoneautomotive.example.nz
        <svg viewBox="0 0 16 16" fill="none" stroke="var(--brand-red)" stroke-width="1.6"><rect x="1.5" y="2.5" width="13" height="9"/><line x1="5" y1="14" x2="11" y2="14"/></svg>
      </li>
      <li>48 Tarn Lane, Harrowby 3597
        <svg viewBox="0 0 16 16" fill="var(--brand-red)"><path d="M8 1 C4.5 1 3 3.5 3 5.8 C3 9 8 15 8 15 C8 15 13 9 13 5.8 C13 3.5 11.5 1 8 1 Z M8 4 A2 2 0 1 0 8 8 A2 2 0 1 0 8 4 Z" fill-rule="evenodd"/></svg>
      </li>
    </ul>
  </section>

  <section class="card card--back" aria-label="Business card back">
    <div class="card__artwork" role="img" aria-label="Faint dark emblem artwork with spanner motif"></div>
    <div class="brand">Keelstone Prime<br>Automotive</div>
    <ul class="service-list">
      <li>Vehicle Servicing</li>
      <li>All Mechanical Repairs</li>
      <li>Warrant of Fitness</li>
      <li>Tyres &amp; Wheel Alignments</li>
      <li>Automotive Diagnostics</li>
      <li>Automotive Parts &amp; Supplies</li>
    </ul>
    <div class="appointment appointment--date">
      <span class="appointment__label">Date</span>
      <span class="appointment__field"></span>
    </div>
    <div class="appointment appointment--time">
      <span class="appointment__label">Time</span>
      <span class="appointment__field"></span>
    </div>
  </section>

</main>
</body>
</html>
```